Small Business Broker Business Card Design

A business card design for a small business brokerage, which is a financial service, not unlike real estate brokerage, but for small businesses such as laundromats, pizza shops, restaurants, cleaners etc. The designs should all be simple, more conservative in nature, using the colors and font of the logo. Again, think real estate Brokerage as a business context
Contact Information for Business Card
Name: Glen R. Harlow. Title: Small Business Advisor. Email: g.harlow@bayfieldcapitalworks.example. Mobile: (555) 274-3918. Office: (555) 806-2147. www.bayfieldcapitalworks.example

```html
<!DOCTYPE html>
<html lang="en">
<head>
<meta charset="utf-8">
<title>Bayfield Capital Works – Business Card</title>
<link href="https://fonts.googleapis.com/css2?family=Montserrat:wght@700;800&family=Arimo:wght@400;700&display=swap" rel="stylesheet">
<style>
  :root {
    --navy: #162f63;
    --green: #7cc13a;
    --white: #ffffff;
    --ink-gray: #5b5e63;
    --stage: #e9eaec;
  }
  * { box-sizing: border-box; margin: 0; padding: 0; }
  html, body { width: 1200px; height: 963px; overflow: hidden; }
  body {
    background: var(--stage);
    position: relative;
    font-family: "Arimo", Arial, sans-serif;
  }
  .card {
    position: absolute;
    left: 260px;
    width: 680px;
    height: 389px;
    border-radius: 20px;
    overflow: hidden;
    box-shadow: 0 6px 22px rgba(0,0,0,0.18);
  }
  .card--front { top: 62px; background: var(--white); }
  .card--back { top: 512px; background: var(--navy); }

  .front-header {
    position: absolute; left: 0; top: 0; width: 100%; height: 118px;
    background: var(--navy);
    border-bottom: 11px solid var(--green);
  }
  .person-name {
    position: absolute; left: 48px; top: 26px;
    font-family: "Montserrat", sans-serif; font-weight: 800;
    font-size: 31px; letter-spacing: 1px; color: var(--white);
    text-transform: uppercase; white-space: nowrap;
  }
  .person-title {
    position: absolute; left: 50px; top: 66px;
    font-size: 18px; color: var(--white);
  }
  .contact-list {
    position: absolute; left: 50px; top: 160px;
    list-style: none; font-size: 18px; line-height: 27px; color: var(--ink-gray);
    white-space: nowrap;
  }
  .contact-label { font-weight: 700; color: var(--green); }

  .brand {
    position: absolute; right: 44px; bottom: 44px;
    display: flex; align-items: center; gap: 10px;
    white-space: nowrap;
  }
  .brand-mark { width: 14px; height: 14px; background: var(--green); flex: none; }
  .brand-name {
    font-family: "Montserrat", sans-serif; font-weight: 800;
    font-size: 20px; letter-spacing: 1.2px; text-transform: uppercase;
    color: var(--navy);
  }
  .card--back .brand {
    right: auto; bottom: auto; left: 50%; top: 50%;
    transform: translate(-50%, -50%);
  }
  .card--back .brand-name { color: var(--white); font-size: 26px; }
  .card--back .brand-mark { width: 16px; height: 16px; }
</style>
</head>
<body>
  <section class="card card--front" aria-label="Business card front">
    <header class="front-header">
      <h1 class="person-name">Glen R. Harlow</h1>
      <p class="person-title">Small Business Advisor</p>
    </header>
    <ul class="contact-list">
      <li><span class="contact-label">O:</span> (555) 806-2147</li>
      <li><span class="contact-label">M:</span> (555) 274-3918</li>
      <li><span class="contact-label">E:</span> g.harlow@bayfieldcapitalworks.example</li>
      <li>www.bayfieldcapitalworks.example</li>
    </ul>
    <div class="brand">
      <span class="brand-mark"></span>
      <p class="brand-name">Bayfield Capital Works, Inc</p>
    </div>
  </section>

  <section class="card card--back" aria-label="Business card back">
    <div class="brand">
      <span class="brand-mark"></span>
      <p class="brand-name">Bayfield Capital Works, Inc</p>
    </div>
  </section>
</body>
</html>
```